business card deign

Logo needs the following on it.
1. attached logo
2. Tagline - "If it keeps the cooler full or the music loud...we bring it!"
3. Name- Dalton Pikes, Founder and CPO
4. Address - 412 E. Carver Avenue, Ste 2207, Brightwater, FL. 33917
5. Phone - 555.318.4726

```html
<!DOCTYPE html>
<html lang="en">
<head>
<meta charset="utf-8">
<title>Tidewell Business Card</title>
<link href="https://fonts.googleapis.com/css2?family=Open+Sans:wght@400;600;700;800&display=swap" rel="stylesheet">
<style>
  :root {
    --stage: #232323;
    --ink: #111111;
    --card-dark: #0c0c0c;
    --paper: #ffffff;
    --rule: #2a2a2a;
    --band: #141414;
  }
  * { box-sizing: border-box; margin: 0; padding: 0; }
  html, body {
    width: 1200px; height: 711px; overflow: hidden;
    background: var(--stage);
    font-family: "Open Sans", Arial, sans-serif;
  }
  .stage {
    position: relative; width: 1200px; height: 711px;
    display: flex; align-items: center; justify-content: center; gap: 40px;
  }
  .card {
    position: relative; width: 540px; height: 309px;
    border-radius: 22px; overflow: hidden;
  }
  .card--front {
    background: var(--card-dark);
    display: flex; align-items: center; justify-content: center;
  }
  .brand { display: flex; align-items: center; gap: 16px; }
  .brand__dot { width: 26px; height: 26px; border-radius: 50%; }
  .brand__name { font-weight: 800; letter-spacing: 12px; }
  .card--front .brand__dot { background: var(--paper); }
  .card--front .brand__name { color: var(--paper); font-size: 44px; }

  .card--back { background: var(--paper); color: var(--ink); }
  .back__logo {
    position: absolute; left: 0; top: 0; width: 245px; height: 245px;
    display: flex; align-items: center; justify-content: center;
  }
  .card--back .brand { gap: 10px; }
  .card--back .brand__dot { width: 16px; height: 16px; background: var(--ink); }
  .card--back .brand__name { color: var(--ink); font-size: 24px; letter-spacing: 7px; }
  .back__divider {
    position: absolute; left: 245px; top: 40px; width: 1px; height: 165px;
    background: var(--rule);
  }
  .contact { position: absolute; left: 278px; top: 56px; }
  .contact__name { font-size: 24px; font-weight: 800; line-height: 1.1; }
  .contact__title { font-size: 13px; font-weight: 700; margin-top: 2px; }
  .contact__list { list-style: none; margin-top: 14px; font-size: 13px; line-height: 1.4; }
  .contact__list li { display: flex; gap: 8px; align-items: flex-start; }
  .contact__list svg { width: 12px; height: 12px; margin-top: 3px; flex: none; }
  .tagline {
    position: absolute; left: 0; right: 0; bottom: 26px; height: 34px;
    background: var(--band); color: var(--paper);
    font-size: 14px; display: flex; align-items: center; padding-left: 34px;
  }
</style>
</head>
<body>
<main class="stage">
  <section class="card card--front" aria-label="Card front">
    <div class="brand">
      <span class="brand__dot"></span>
      <span class="brand__name">TIDEWELL</span>
    </div>
  </section>

  <section class="card card--back" aria-label="Card back">
    <div class="back__logo">
      <div class="brand">
        <span class="brand__dot"></span>
        <span class="brand__name">TIDEWELL</span>
      </div>
    </div>
    <div class="back__divider"></div>
    <div class="contact">
      <h1 class="contact__name">Dalton Pikes</h1>
      <p class="contact__title">Founder and CPO</p>
      <ul class="contact__list">
        <li>
          <svg viewBox="0 0 12 12"><path d="M2.5 1h2l1 2.5-1.3.9a6 6 0 0 0 3.4 3.4l.9-1.3L11 7.5v2A1.5 1.5 0 0 1 9.5 11 8.5 8.5 0 0 1 1 2.5 1.5 1.5 0 0 1 2.5 1z" fill="none" stroke="#111" stroke-width="1.2"/></svg>
          <span>555.318.4726</span>
        </li>
        <li>
          <svg viewBox="0 0 12 12"><path d="M6 11s-3.5-3.6-3.5-6.2a3.5 3.5 0 0 1 7 0C9.5 7.4 6 11 6 11z" fill="none" stroke="#111" stroke-width="1.2"/><circle cx="6" cy="4.8" r="1.2" fill="#111"/></svg>
          <span>412 E. Carver Avenue,<br>Ste 2207, Brightwater, FL. 33917</span>
        </li>
      </ul>
    </div>
    <p class="tagline">If it keeps the cooler full or the music loud...we bring it!</p>
  </section>
</main>
</body>
</html>
```